Salon and Spa Distributor Business Card

Need a business card. We are are distributor in the salon and spa industry. We identify with natural beauty. Need a card with:
Company Name: Petal Quarry"
Title: "President & CEO"
Address
Company Phone number
email
website
Tag Line:" The Professional Salon Source"

Industry/Entity Type

Business

Contact Information for Business Card

Name: Dov Strommen
Title: "President & CEO"
Address: 31 Harlow Ln, Bexmoor, NJ 07813
Company Phone number: 800-463-5918
email: dovstrommen@petalquarry.example
website: www.petalquarry.example

Requirements
Should not have
• No black backgrounds

```html
<!DOCTYPE html>
<html lang="en">
<head>
<meta charset="utf-8">
<title>Petal Quarry — Business Card</title>
<link href="https://fonts.googleapis.com/css2?family=Source+Sans+3:wght@300;400;600&display=swap" rel="stylesheet">
<style>
  :root {
    --page-bg: #eeeeec;
    --card-green-top: #63bc47;
    --card-green-mid: #58b244;
    --card-green-bottom: #2f8a3d;
    --forest: #076b3a;
    --leaf-white: #ffffff;
    --text-white: #ffffff;
    --text-soft: rgba(255, 255, 255, 0.9);
  }
  html, body {
    margin: 0;
    padding: 0;
    width: 1200px;
    height: 900px;
    overflow: hidden;
    background: var(--page-bg);
  }
  .business-card {
    position: absolute;
    left: 100px;
    top: 142px;
    width: 1000px;
    height: 616px;
    overflow: hidden;
    background: linear-gradient(180deg, var(--card-green-top) 0%, var(--card-green-mid) 55%, var(--card-green-bottom) 100%);
    color: var(--text-white);
    font-family: "Source Sans 3", "Myriad Pro", sans-serif;
    box-shadow: 0 10px 30px rgba(0, 0, 0, 0.12);
  }
  .brand-illustration {
    position: absolute;
    right: 0;
    top: 0;
    width: 640px;
    height: 616px;
  }
  .brand {
    position: absolute;
    left: 50px;
    top: 80px;
  }
  .company-name {
    margin: 0;
    font-weight: 300;
    font-size: 52px;
    line-height: 1;
    letter-spacing: 0.3px;
  }
  .tagline {
    margin: 10px 0 0 2px;
    font-weight: 400;
    font-size: 21px;
    line-height: 1.2;
    letter-spacing: 0.4px;
    color: var(--text-soft);
  }
  .person {
    position: absolute;
    left: 51px;
    top: 210px;
  }
  .person-name {
    margin: 0;
    font-weight: 600;
    font-size: 34px;
    line-height: 1.1;
  }
  .person-title {
    margin: 2px 0 0;
    font-weight: 400;
    font-size: 24px;
    line-height: 1.2;
  }
  .address {
    position: absolute;
    left: 52px;
    top: 332px;
    margin: 0;
    font-style: normal;
    font-size: 25px;
    line-height: 40px;
  }
  .contact-list {
    position: absolute;
    left: 52px;
    top: 454px;
    margin: 0;
    padding: 0;
    list-style: none;
    font-size: 25px;
    line-height: 41px;
  }
  .contact-item {
    display: flex;
    align-items: center;
    gap: 14px;
  }
  .contact-icon {
    width: 20px;
    height: 20px;
    flex: none;
  }
</style>
</head>
<body>
  <article class="business-card">
    <svg class="brand-illustration" viewBox="0 0 640 616" role="img" aria-label="Illustration area: woman's profile with flowing hair and leaves in white and forest green">
      <defs>
        <linearGradient id="illustration-fill" x1="0" y1="0" x2="1" y2="1">
          <stop offset="0" stop-color="#8fd07a" stop-opacity="0.55"/>
          <stop offset="0.45" stop-color="#ffffff" stop-opacity="0.9"/>
          <stop offset="1" stop-color="#076b3a"/>
        </linearGradient>
      </defs>
      <path d="M300 0 H640 V616 H320 C420 520 380 400 260 330 C380 300 470 180 300 0 Z" fill="url(#illustration-fill)"/>
    </svg>

    <header class="brand">
      <h1 class="company-name">PetalQuarry</h1>
      <p class="tagline">The Professional Salon Source</p>
    </header>

    <div class="person">
      <p class="person-name">Dov Strommen</p>
      <p class="person-title">President &amp; CEO</p>
    </div>

    <address class="address">
      31 Harlow Ln,<br>
      Bexmoor, NJ 07813
    </address>

    <ul class="contact-list">
      <li class="contact-item">
        <svg class="contact-icon" viewBox="0 0 20 20" aria-hidden="true"><path d="M5 2 L8 2 L9 6 L7 8 C8 11 9 12 12 13 L14 11 L18 12 L18 15 C18 17 16 18 14 18 C8 17 3 12 2 6 C2 4 3 2 5 2 Z" fill="var(--text-white)"/></svg>
        <span>800-463-5918</span>
      </li>
      <li class="contact-item">
        <svg class="contact-icon" viewBox="0 0 20 20" aria-hidden="true"><rect x="1" y="4" width="18" height="12" fill="var(--text-white)"/><path d="M1 4 L10 11 L19 4" fill="none" stroke="var(--card-green-mid)" stroke-width="1.6"/></svg>
        <span>dovstrommen@petalquarry.example</span>
      </li>
      <li class="contact-item">
        <svg class="contact-icon" viewBox="0 0 20 20" aria-hidden="true"><circle cx="10" cy="10" r="9" fill="var(--text-white)"/><path d="M6 6 C8 5 9 7 8 9 C7 11 9 12 10 14 M12 4 C14 6 15 8 13 10" fill="none" stroke="var(--card-green-bottom)" stroke-width="1.6"/></svg>
        <span>www.petalquarry.example</span>
      </li>
    </ul>
  </article>
</body>
</html>
```